Australian Trucking Company Requires Professional Looking Stationary

We require a professional looking stationary design that incorporates our newly designed logo.

Our business, called "Brell Haulage Contracting", provides contracting work, transport and logistics to business in Western Australia particularly with links to the mining sector.

We are a small business looking to expand and our new logo and our new stationary will help develop our brand image in our market place.

Target Market(s)

Businesses and Corporation with links to the Mining Sector

Industry/Entity Type

Small Business

Requirements
Must have
• The letterhead must have the following details:
The new logo

Text saying: "Brell Holdings Pty Ltd (ACN 582 316 907) ATF The Brell Discretionary Trust T/AS"
"ABN 71 834 209 553"
Address "P.O Box 817 Wattlegrove WA, 6958"
Phone: 08 9352 7140
Email: brellhaul@mailbox-example.com.au

The text on the letterhead should be editable as the details are likely to change in the near future. Provision should be made for a website address all though one isn't available at the moment.

The styling, layout and font text is entirely up to the designer.

```html
<!DOCTYPE html>
<html lang="en">
<head>
<meta charset="utf-8">
<title>Brell Haulage Contracting – Business Card</title>
<link rel="stylesheet" href="https://fonts.googleapis.com/css2?family=Open+Sans:wght@400;600;700&display=swap">
<style>
  :root {
    --stage: #e8e5e1;
    --card: #ffffff;
    --ink: #2a2a2a;
    --ink-soft: #3a3a3a;
    --brand-red: #d7202a;
    --brand-red-deep: #b3131c;
    --band-dark: #1c1c1c;
    --band-grey: #6a6a6a;
    --art-tone: #cfcfcf;
    --art-tone-dark: #9a9a9a;
  }
  * { box-sizing: border-box; margin: 0; padding: 0; }
  html, body {
    width: 1200px; height: 426px; overflow: hidden;
    background: var(--stage);
    font-family: "Open Sans", Arial, sans-serif;
    color: var(--ink);
  }
  .canvas { position: relative; width: 1200px; height: 426px; }
  .card {
    position: absolute; top: 50px;
    width: 516px; height: 296px;
    background: var(--card);
    border-radius: 18px;
    overflow: hidden;
    box-shadow: 0 4px 14px rgba(0,0,0,.18);
  }
  .card--front { left: 52px; }
  .card--back { left: 603px; width: 545px; }

  .art {
    position: absolute;
    border-radius: 10px;
    background: linear-gradient(135deg, var(--art-tone), var(--art-tone-dark));
  }
  .art--logo-truck { left: 28px; top: 25px; width: 106px; height: 88px; }
  .art--side-truck { left: 396px; top: 120px; width: 112px; height: 92px; }
  .art--hero-truck {
    left: 148px; top: 40px; width: 300px; height: 222px;
    background: linear-gradient(135deg, #3a3a3a, #0f0f0f);
  }

  .brand-name {
    position: absolute; left: 154px; top: 32px;
    font-weight: 700; font-size: 25px; line-height: 27px;
    color: var(--brand-red);
    text-transform: uppercase; letter-spacing: .5px;
  }

  .person { position: absolute; left: 32px; top: 155px; font-size: 16px; font-weight: 600; color: var(--ink-soft); }
  .person__role { font-size: 12px; font-weight: 400; }

  .contact { position: absolute; left: 28px; list-style: none; font-size: 12px; color: var(--ink-soft); }
  .contact li { display: flex; align-items: center; gap: 5px; height: 16px; }
  .contact svg { width: 11px; height: 11px; fill: var(--brand-red); flex: none; }
  .contact--reach { top: 200px; }
  .contact--post { top: 242px; }

  .entity {
    position: absolute; left: 270px; top: 212px; width: 230px;
    text-align: center; font-size: 11px; line-height: 16px; color: var(--ink);
  }

  .band { position: absolute; left: 0; bottom: 0; width: 516px; height: 30px; }
</style>
</head>
<body>
<main class="canvas">

  <section class="card card--front" aria-label="Business card front">
    <div class="art art--logo-truck" role="img" aria-label="Grey truck illustration beside the company name"></div>
    <h1 class="brand-name">Brell<br>Haulage<br>Contracting</h1>

    <p class="person">Persons name, <span class="person__role">Manager</span></p>

    <ul class="contact contact--reach">
      <li>
        <svg viewBox="0 0 24 24" aria-hidden="true"><path d="M6.6 10.8a15 15 0 0 0 6.6 6.6l2.2-2.2a1 1 0 0 1 1-.25 11.4 11.4 0 0 0 3.6.57 1 1 0 0 1 1 1V20a1 1 0 0 1-1 1A17 17 0 0 1 3 4a1 1 0 0 1 1-1h3.5a1 1 0 0 1 1 1c0 1.25.2 2.45.57 3.57a1 1 0 0 1-.25 1z"/></svg>
        08 9352 7140
      </li>
      <li>
        <svg viewBox="0 0 24 24" aria-hidden="true"><path d="M2 5h20v14H2zm2 2v.5l8 5 8-5V7zm0 2.8V17h16V9.8l-8 5z"/></svg>
        brellhaul@mailbox-example.com.au
      </li>
    </ul>
    <ul class="contact contact--post">
      <li>
        <svg viewBox="0 0 24 24" aria-hidden="true"><path d="M12 3 2 12h3v9h5v-6h4v6h5v-9h3z"/></svg>
        P.O Box 817 Wattlegrove WA, 6958
      </li>
    </ul>

    <div class="art art--side-truck" role="img" aria-label="Black truck illustration, front three-quarter view"></div>

    <p class="entity">
      Brell Holdings Pty Ltd (ACN 582 316 907)<br>
      ATF The Brell Discretionary Trust T/AS<br>
      ABN 71 834 209 553
    </p>

    <svg class="band" viewBox="0 0 516 30" preserveAspectRatio="none" aria-hidden="true">
      <defs>
        <linearGradient id="bandDark" x1="0" x2="1" y1="0" y2="0">
          <stop offset="0" stop-color="var(--band-dark)"/>
          <stop offset="1" stop-color="var(--band-grey)"/>
        </linearGradient>
        <linearGradient id="bandRed" x1="0" x2="1" y1="0" y2="0">
          <stop offset="0" stop-color="var(--brand-red)"/>
          <stop offset="1" stop-color="var(--brand-red-deep)"/>
        </linearGradient>
      </defs>
      <polygon points="0,0 238,0 254,30 0,30" fill="url(#bandDark)"/>
      <polygon points="232,0 516,0 516,30 248,30" fill="url(#bandRed)"/>
    </svg>
  </section>

  <section class="card card--back" aria-label="Business card back">
    <div class="art art--hero-truck" role="img" aria-label="Large black truck silhouette illustration"></div>
  </section>

</main>
</body>
</html>
```